Theatre Company needs poster for a Christmas show.

We need a poster for an annual Christmas musical show call "The Frosted Hour". The style is Jazzy/Lounge Christmas songs. The poster should be a mid-centry modern, Pale Ledger-style design. I have attached the past year's poster for reference. The poster should include "Brindlewood Performance Circle presents The Frosted Hour" the date "December 18th, 2015" our phone number "512-634-2817 ext 204" and our website "brindlewood-stage.org". The poster should also include the logos of our title sponsors (attached).

Target Market(s)

Lakeway, Texas residents, Adults, 21+

Industry/Entity Type

It Company

Font styles to use
Sans Serif

Requirements
Must have
• Brindlewood logo
• Show title "The Frosted Hour"
• Date: December 18th, 2015
• Phone number: 512-634-2817 ext 204
• Web site: brindlewood-stage.org
• Sponsor logos at the bottom (attached)
• Mid-century modern, Pale Ledger-style design
• Christmas/Winter colors
Nice to have
• Singer/piano/microphone imagery
• cocktail imagery

```html
<!DOCTYPE html>
<html lang="en">
<head>
<meta charset="utf-8">
<title>The Frosted Hour — Brindlewood Performance Circle</title>
<link href="https://fonts.googleapis.com/css2?family=Oswald:wght@500;700&family=Lobster&family=Open+Sans:wght@600;800&display=swap" rel="stylesheet">
<style>
  :root {
    --red-deep: #b9141b;
    --red: #dd2a1c;
    --orange: #ee7a1e;
    --amber: #f4b12b;
    --gold: #f7d234;
    --pale-gold: #fbe98a;
    --green: #2f7d2a;
    --green-dark: #1d5a1a;
    --navy: #1d2a57;
    --ink: #1a1a1a;
    --white: #ffffff;
    --star: rgba(255, 240, 220, 0.75);
  }
  html, body {
    margin: 0;
    padding: 0;
    overflow: hidden;
    background: var(--white);
  }
  .poster {
    position: relative;
    width: 849px;
    height: 1200px;
    overflow: hidden;
    background:
      radial-gradient(ellipse at 85% 85%, var(--gold) 0%, transparent 55%),
      linear-gradient(115deg, var(--red-deep) 0%, var(--red) 30%, var(--orange) 62%, var(--amber) 100%);
    font-family: "Open Sans", sans-serif;
  }
  .presenter-line {
    position: absolute;
    top: 26px;
    left: 0;
    width: 100%;
    margin: 0;
    text-align: center;
    white-space: nowrap;
    font-family: "Oswald", sans-serif;
    font-weight: 700;
    font-size: 34px;
    letter-spacing: 1px;
    text-transform: uppercase;
    color: var(--amber);
    -webkit-text-stroke: 1.5px var(--red-deep);
  }
  .singer-photo {
    position: absolute;
    left: 60px;
    top: 95px;
    width: 520px;
    height: 990px;
    background:
      radial-gradient(ellipse at 55% 22%, #f3d7b8 0%, #d99a6e 30%, transparent 60%),
      linear-gradient(180deg, rgba(240, 200, 160, 0.85) 0%, rgba(170, 30, 25, 0.9) 55%, rgba(120, 15, 18, 0.9) 100%);
    border-radius: 40% 40% 0 0 / 18% 18% 0 0;
    opacity: 0.92;
  }
  .stars {
    position: absolute;
    inset: 0;
    pointer-events: none;
  }
  .show-title {
    position: absolute;
    left: 230px;
    top: 430px;
    width: 580px;
    margin: 0;
    transform: rotate(-18deg);
    transform-origin: center;
    font-family: "Lobster", cursive;
    font-weight: 400;
    line-height: 0.95;
    text-align: center;
    white-space: nowrap;
    color: var(--gold);
    -webkit-text-stroke: 3px var(--green);
    text-shadow: 4px 4px 0 var(--green-dark);
  }
  .show-title .line-one { display: block; font-size: 110px; }
  .show-title .line-two { display: block; font-size: 170px; padding-left: 60px; }
  .show-date {
    position: absolute;
    left: 430px;
    top: 880px;
    margin: 0;
    padding: 4px 16px;
    transform: rotate(-14deg);
    background: var(--pale-gold);
    white-space: nowrap;
    font-family: "Oswald", sans-serif;
    font-weight: 700;
    font-size: 38px;
    color: var(--orange);
    -webkit-text-stroke: 1px var(--red);
    text-transform: uppercase;
  }
  .footer {
    position: absolute;
    left: 0;
    bottom: 0;
    width: 100%;
    height: 112px;
    background: var(--white);
    display: flex;
    align-items: center;
    justify-content: space-between;
    padding: 0 22px 0 26px;
    box-sizing: border-box;
  }
  .sponsors {
    display: flex;
    align-items: center;
    gap: 28px;
  }
  .sponsor {
    display: flex;
    align-items: center;
    gap: 8px;
    white-space: nowrap;
    font-weight: 800;
    font-size: 16px;
    line-height: 1.1;
    color: var(--navy);
  }
  .sponsor-mark {
    width: 14px;
    height: 14px;
    flex: none;
    background: var(--navy);
  }
  .sponsor-mark.round { border-radius: 50%; background: var(--orange); }
  .sponsor-stack { display: flex; flex-direction: column; }
  .contact {
    text-align: right;
    color: var(--ink);
    font-weight: 800;
    white-space: nowrap;
    line-height: 1.15;
  }
  .contact-phone { font-size: 24px; margin: 0; }
  .contact-web { font-size: 30px; margin: 0; letter-spacing: -0.5px; }
</style>
</head>
<body>
<main class="poster">
  <h2 class="presenter-line">Brindlewood Performance Circle Presents</h2>

  <div class="singer-photo" role="img" aria-label="Photograph of a lounge singer in a red halter dress, halftone tinted in reds and oranges"></div>

  <svg class="stars" width="849" height="1200" viewBox="0 0 849 1200" aria-hidden="true">
    <g fill="var(--star)">
      <polygon points="705,400 712,418 731,418 716,429 722,447 705,436 688,447 694,429 679,418 698,418"/>
      <polygon points="780,980 785,992 798,992 788,1000 792,1012 780,1004 768,1012 772,1000 762,992 775,992"/>
      <polygon points="520,995 524,1004 534,1004 526,1010 529,1019 520,1013 511,1019 514,1010 506,1004 516,1004"/>
      <polygon points="660,1040 663,1047 671,1047 665,1052 667,1060 660,1055 653,1060 655,1052 649,1047 657,1047"/>
    </g>
    <g stroke="var(--star)" stroke-width="3" stroke-linecap="round">
      <path d="M505 1045 v16 M497 1053 h16"/>
    </g>
  </svg>

  <h1 class="show-title">
    <span class="line-one">The Frosted</span>
    <span class="line-two">Hour</span>
  </h1>

  <p class="show-date">December 18th, 2015</p>

  <footer class="footer">
    <div class="sponsors">
      <div class="sponsor"><span class="sponsor-mark round"></span>Stepline Dance</div>
      <div class="sponsor"><span class="sponsor-mark"></span>Harlow Hall</div>
      <div class="sponsor sponsor-stack"><span>Marin Lens</span><span>Photography</span></div>
    </div>
    <div class="contact">
      <p class="contact-phone">512-634-2817 EXT 204</p>
      <p class="contact-web">brindlewood-stage.org</p>
    </div>
  </footer>
</main>
</body>
</html>
```